Label Design Project

I will need 3 different labels:Using the Halvorsen Outreach Ventures logo on the front of each with different names of the jams on each. One label should indicate Honey My Muffin Ginger Plum Jam, One label should be Plum Fun For All and one label for Wexmoor Toffee. I would like for the label to wrap around and not 2 separate labels. except for the Wexmoor Toffee. This label should have portrait layout or two labels with the name of the Wexmoor Toffee on the front and the story and nutritional label on back. Jar dimensions for the label: W 2-3/4" x H 3-5/8 and L 8" Each Jam label should have the Outreach story, Nutrition, and a logo. The nuts label will have the logo with the name of the nut (Wexmoor Toffee) on the front and story, nutritional label and ingredients on the back. This label should be W 2 1/2" and L 3". I've attached a sample of what I have however, the text is too small.

```html
<!DOCTYPE html>
<html lang="en">
<head>
<meta charset="utf-8">
<title>Honey My Muffin Ginger Plum Jam – Wrap Label</title>
<link href="https://fonts.googleapis.com/css2?family=Noto+Serif:wght@400;500&family=Rochester&family=Roboto:wght@400;700&display=swap" rel="stylesheet">
<style>
  :root{
    --wine:#7d1a2e;
    --royal:#1a4fa0;
    --sun:#f2c21b;
    --ink:#2e2e2e;
    --paper:#ffffff;
    --page:#f4f4f4;
  }
  *{box-sizing:border-box;margin:0;padding:0}
  html,body{width:1200px;height:1200px;overflow:hidden;background:var(--page)}
  .canvas{position:relative;width:1200px;height:1200px}
  .wrap-label{
    position:absolute;left:30px;top:444px;width:1140px;height:312px;
    background:var(--paper);border:1px solid #555;overflow:hidden;
  }
  .band{
    position:absolute;left:0;right:0;bottom:0;height:46px;background:var(--wine);
    color:#fff;font-family:"Noto Serif",serif;white-space:nowrap;
  }
  .band .flavour{position:absolute;left:0;width:452px;text-align:center;top:2px;font-size:35px;line-height:40px}
  .band .thanks-line{position:absolute;left:470px;width:650px;text-align:center;top:9px;font-size:23px;line-height:30px}

  .brand{
    position:absolute;left:0;top:30px;width:452px;height:170px;
    display:flex;flex-direction:column;align-items:center;justify-content:center;gap:12px;
  }
  .brand-dot{width:46px;height:46px;border-radius:50%;background:var(--sun)}
  .brand-name{
    font-family:"Noto Serif",serif;font-weight:400;color:var(--royal);
    font-size:32px;line-height:1.1;text-align:center;
  }
  .product-name{
    position:absolute;left:0;width:452px;top:212px;text-align:center;white-space:nowrap;
    font-family:"Rochester",cursive;color:var(--wine);font-size:38px;line-height:48px;
  }

  .ingredients{
    position:absolute;left:480px;top:12px;height:254px;width:40px;
    writing-mode:vertical-rl;transform:rotate(180deg);
    font-family:"Roboto",sans-serif;font-size:7.4px;line-height:9.6px;color:var(--ink);text-align:justify;
  }
  .ingredients b{font-weight:700}

  .nutrition{
    position:absolute;left:524px;top:14px;width:117px;height:250px;
    border:1px solid #999;padding:2px 3px;font-family:"Roboto",sans-serif;color:#111;
    font-size:5.6px;line-height:7.6px;overflow:hidden;
  }
  .nutrition h3{font-size:12px;line-height:13px;font-weight:700;border-bottom:1px solid #111}
  .nutrition .thick{border-bottom:4px solid #111;padding-bottom:1px}
  .nutrition .mid{border-bottom:2px solid #111}
  .nutrition .row{display:flex;justify-content:space-between;border-bottom:.5px solid #888}
  .nutrition .row.in{padding-left:7px}
  .nutrition .row.in2{padding-left:14px}
  .nutrition .cal{display:flex;justify-content:space-between;align-items:flex-end;font-size:10px;line-height:12px;font-weight:700}
  .nutrition .cal span:last-child{font-size:14px}
  .nutrition .right{text-align:right}
  .nutrition .foot{font-size:4.3px;line-height:5.4px;margin-top:3px}

  .web{
    position:absolute;left:648px;top:14px;height:250px;
    writing-mode:vertical-rl;transform:rotate(180deg);text-align:center;white-space:nowrap;
    font-family:"Roboto",sans-serif;font-weight:700;color:var(--wine);font-size:15px;line-height:16px;
  }

  .story{position:absolute;left:706px;top:10px;width:398px}
  .story h2{font-family:"Rochester",cursive;font-weight:400;color:var(--wine);font-size:28px;line-height:36px}
  .story p{
    font-family:"Noto Serif",serif;color:var(--ink);font-size:12.4px;line-height:18px;
    text-align:justify;margin-top:2px;
  }
  .verse{
    margin-top:6px;font-family:"Rochester",cursive;color:var(--wine);
    font-size:18px;line-height:26px;text-align:center;white-space:nowrap;
  }
</style>
</head>
<body>
<div class="canvas">
  <section class="wrap-label" aria-label="Honey My Muffin Ginger Plum Jam wrap-around label">

    <div class="brand">
      <span class="brand-dot"></span>
      <div class="brand-name">Halvorsen Outreach<br>Ventures</div>
    </div>
    <div class="product-name">Honey My Muffin</div>

    <div class="ingredients"><b>INGREDIENTS:</b> Sugar, Plums, Lemon Juice (Filtered Water, Lemon Juice Concentrate, Sodium Bisulfite (Preservative), Sodium Benzoate (Preservative)), Lemon Oil, Ginger, Pectin.</div>

    <div class="nutrition">
      <h3>Nutrition Facts</h3>
      <div>8 servings per container</div>
      <div class="thick"><b>Serving size 2 tablespoons (34g)</b></div>
      <div style="margin-top:2px"><b>Amount per serving</b></div>
      <div class="cal mid"><span>Calories</span><span>90</span></div>
      <div class="right"><b>% Daily Value*</b></div>
      <div class="row"><span><b>Total Fat</b> 0g</span><span>0%</span></div>
      <div class="row in"><span>Saturated Fat 0g</span><span>0%</span></div>
      <div class="row in"><span><i>Trans</i> Fat 0g</span><span></span></div>
      <div class="row"><span><b>Cholesterol</b> 0mg</span><span>0%</span></div>
      <div class="row"><span><b>Sodium</b> 0mg</span><span>0%</span></div>
      <div class="row"><span><b>Total Carbohydrate</b> 23g</span><span>8%</span></div>
      <div class="row in"><span>Dietary Fiber 0g</span><span>0%</span></div>
      <div class="row in"><span>Total Sugars 23g</span><span></span></div>
      <div class="row in2"><span>Includes 22g Added Sugars</span><span>45%</span></div>
      <div class="row thick"><span><b>Protein</b> 0g</span><span></span></div>
      <div class="row"><span>Vitamin D 0mcg</span><span>0%</span></div>
      <div class="row"><span>Calcium 1mg</span><span>0%</span></div>
      <div class="row"><span>Iron 0mg</span><span>0%</span></div>
      <div class="row mid"><span>Potassium 21mg</span><span>0%</span></div>
      <div class="foot">*The % Daily Value tells you how much a nutrient in a serving of food contributes to a daily diet. 2,000 calories a day is used for general nutrition advice.</div>
      <div class="foot">Calories per gram:<br>Fat 9 • Carbohydrate 4 • Protein 4</div>
    </div>

    <div class="web">www.halvorsenoutreach.org</div>

    <div class="story">
      <h2>Thank you!</h2>
      <p>The product you just purchased is hand-crafted from the finest ingredients and packaged with loving care by friends of Halvorsen Outreach. Your purchase supports the Outreach’ Social Enterprise Programs, which provide poverty-stricken families in the Deep South with the skills and opportunities to work their way from poverty to independence.</p>
      <div class="verse">You shall freely open your hand to your brother,<br>to your needy and poor in your land. –<br>Deuteronomy 15:11</div>
    </div>

    <div class="band">
      <div class="flavour">Ginger Plum Jam</div>
      <div class="thanks-line">Please accept our deepest thanks for your support!</div>
    </div>
  </section>
</div>
</body>
</html>
```